Market Research firm needs updated business cards with new logo

We need the logo to be included somewhere on the card (attached). We would also like the phrases "Independent, Objective, Comprehensive" and "Research You Can Trust" somewhere on the card. Front or back. Our colors are hex codes 6075a7, e48d25 and 5a5b5b. Though you are certainly not limited to those shades, whatever you produce should coordinate with them. I have also attached our favicon. Feel free to use it in your design, but please do not use it to replace the full logo.

Contact Information for Business Card

see project description

Font styles to use
Other font styles liked:
• Open Sans

Requirements
Must have
• the logo
• We use Open Sans font

```html
<!DOCTYPE html>
<html lang="en">
<head>
<meta charset="utf-8">
<title>Halvern Research – Business Card</title>
<link rel="stylesheet" href="https://fonts.googleapis.com/css2?family=Open+Sans:wght@300;400;600&family=Lato:wght@400;700&display=swap">
<style>
  :root {
    --slate: #6c7a8b;
    --slate-light: #7d8a9a;
    --orange: #f0821e;
    --ink: #2b2b2b;
    --paper: #ffffff;
    --backdrop: #1c1c1e;
  }
  * { box-sizing: border-box; margin: 0; padding: 0; }
  html, body { width: 1200px; height: 912px; overflow: hidden; }
  body { background: var(--backdrop); font-family: "Lato", "Open Sans", sans-serif; position: relative; }

  .card { position: absolute; width: 560px; height: 320px; overflow: hidden; }

  /* Front */
  .card-front { left: 60px; top: 70px; background: var(--slate); }
  .card-front .brand {
    position: absolute; left: 70px; top: 100px;
    font-family: "Open Sans", sans-serif; font-weight: 300; font-size: 58px;
    color: var(--paper); letter-spacing: -1px;
  }
  .card-front .tagline {
    position: absolute; left: 72px; font-family: "Open Sans", sans-serif;
    color: var(--paper); text-transform: uppercase; font-size: 13px; letter-spacing: 0.5px;
  }
  .card-front .tagline-trust { top: 196px; left: 150px; }
  .card-front .tagline-values { top: 222px; }
  .dot { display: inline-block; width: 6px; height: 6px; border-radius: 50%; background: var(--orange); margin: 0 6px 2px; }

  /* Back */
  .card-back { left: 580px; top: 520px; background: var(--paper); }
  .card-back .brand {
    position: absolute; left: 36px; top: 56px;
    font-family: "Open Sans", sans-serif; font-weight: 300; font-size: 40px; color: var(--slate); letter-spacing: -0.5px;
  }
  .holder { position: absolute; right: 36px; top: 40px; text-align: right; }
  .holder .name { color: var(--orange); font-weight: 700; font-size: 20px; }
  .holder .role { color: var(--ink); font-size: 13px; margin-top: 2px; }
  .address { position: absolute; right: 36px; top: 118px; text-align: right; font-size: 13px; color: var(--ink); line-height: 1.4; }
  .rule { position: absolute; left: 36px; top: 110px; width: 488px; height: 1px; background: var(--orange); }
  .contacts { position: absolute; left: 36px; top: 150px; list-style: none; font-size: 14px; color: var(--ink); line-height: 1.55; }
  .contacts li { display: flex; align-items: center; gap: 10px; }
  .contacts svg { width: 13px; height: 13px; fill: var(--orange); }
  .footer-band { position: absolute; left: 0; bottom: 0; width: 560px; height: 120px; }
  .web { position: absolute; right: 24px; bottom: 56px; color: var(--paper); font-size: 13px; }
</style>
</head>
<body>
  <section class="card card-front">
    <div class="brand">Halvern Research</div>
    <p class="tagline tagline-trust">Research you can trust</p>
    <p class="tagline tagline-values">Independent<span class="dot"></span>Objective<span class="dot"></span>Comprehensive</p>
  </section>

  <section class="card card-back">
    <div class="brand">Halvern Research</div>
    <div class="holder">
      <div class="name">Daniel Orvik</div>
      <div class="role">Chief Executive Officer</div>
    </div>
    <div class="rule"></div>
    <div class="address">48 Riverside Court<br>Springfield, ST 00000</div>
    <ul class="contacts">
      <li><svg viewBox="0 0 24 24"><path d="M6.6 10.8a15 15 0 0 0 6.6 6.6l2.2-2.2c.3-.3.7-.4 1-.2 1.1.4 2.3.6 3.6.6.6 0 1 .4 1 1V20c0 .6-.4 1-1 1A17 17 0 0 1 3 4c0-.6.4-1 1-1h3.5c.6 0 1 .4 1 1 0 1.3.2 2.5.6 3.6.1.3 0 .7-.2 1z"/></svg>+1 (555) 014-2200</li>
      <li><svg viewBox="0 0 24 24"><path d="M6 2h12v5H6zM4 8h16a2 2 0 0 1 2 2v7h-4v5H6v-5H2v-7a2 2 0 0 1 2-2zm4 8v4h8v-4z"/></svg>+1 (555) 014-2201</li>
      <li><svg viewBox="0 0 24 24"><path d="M2 5h20v14H2zm2 2v.5l8 5 8-5V7z"/></svg>sales@halvern-research.com</li>
    </ul>
    <svg class="footer-band" viewBox="0 0 560 120" preserveAspectRatio="none" aria-hidden="true">
      <path d="M0 92 L300 92 C340 92 360 40 400 40 L560 40 L560 120 L0 120 Z" fill="var(--slate)"/>
      <path d="M0 84 L290 84 C320 84 340 60 360 50 C345 64 330 92 300 96 L0 98 Z" fill="var(--orange)"/>
      <rect x="0" y="100" width="560" height="4" fill="var(--paper)"/>
    </svg>
    <div class="web">www.halvern-research.com</div>
  </section>
</body>
</html>
```